Business IT Services Billboard to attract local small businesses

We are Brivoqua, a premier Managed Service Provider (MSP) specializing in comprehensive IT services and VOIP phone solutions exclusively for businesses. Our goal is to create a dynamic and visually engaging billboard advertisement that not only highlights our cutting-edge IT solutions but also emphasizes our state-of-the-art VOIP phone services. This billboard should communicate our commitment to providing innovative, reliable, and holistic technology solutions.
See the attached supporting documentation.
Target Market(s)
small business
Industry/Entity Type
Information Technology
Colors
Designer to choose colors to be used in the design.
Look and feel
Each slider illustrates characteristics of the customer's brand and the style your logo design should communicate.

```html
<!DOCTYPE html>
<html lang="en">
<head>
<meta charset="utf-8">
<title>Brivoqua – IT and VOIP Services Billboard</title>
<link rel="stylesheet" href="https://fonts.googleapis.com/css2?family=Archivo+Black&family=Poppins:wght@300;400;600;700&display=swap">
<style>
  :root {
    --page-bg: #c2c2c2;
    --board-white: #ffffff;
    --brand-blue: #1b74bf;
    --sky-blue: #2b9af0;
    --deep-navy: #0b2a58;
    --photo-mid: #1d4f8c;
    --photo-light: #3f86c9;
    --ink: #161616;
  }
  * { margin: 0; padding: 0; box-sizing: border-box; }
  html, body {
    width: 984px;
    height: 1200px;
    overflow: hidden;
    background: var(--page-bg);
  }
  .billboard {
    position: absolute;
    left: 42px;
    top: 407px;
    width: 900px;
    height: 386px;
    background: var(--board-white);
    box-shadow: 0 4px 14px rgba(0,0,0,0.25);
    overflow: hidden;
  }
  .brand-name {
    position: absolute;
    left: 30px;
    top: 72px;
    width: 190px;
    text-align: center;
    font-family: "Archivo Black", sans-serif;
    font-size: 34px;
    line-height: 1;
    color: var(--brand-blue);
  }
  .headline {
    position: absolute;
    left: 244px;
    top: 26px;
    width: 610px;
    height: 150px;
  }
  .headline-lead {
    font-family: "Poppins", sans-serif;
    font-weight: 400;
    fill: var(--ink);
  }
  .headline-main {
    font-family: "Archivo Black", sans-serif;
    fill: var(--brand-blue);
  }
  .headline-sub {
    font-family: "Archivo Black", sans-serif;
    fill: var(--ink);
  }
  .tagline-band {
    position: absolute;
    left: 35px;
    top: 183px;
    width: 824px;
    height: 51px;
  }
  .tagline-text {
    position: absolute;
    left: 35px;
    top: 183px;
    width: 824px;
    height: 51px;
    display: flex;
    align-items: center;
    justify-content: center;
    font-family: "Poppins", sans-serif;
    font-weight: 600;
    font-size: 20.5px;
    color: var(--board-white);
    white-space: nowrap;
  }
  .cta-panel {
    position: absolute;
    left: 0;
    top: 241px;
    width: 900px;
    height: 145px;
    background: var(--deep-navy);
  }
  .team-photo {
    position: absolute;
    right: 0;
    top: 0;
    width: 430px;
    height: 145px;
    background:
      radial-gradient(ellipse at 60% 55%, var(--photo-light) 0%, transparent 60%),
      linear-gradient(90deg, var(--deep-navy) 0%, var(--photo-mid) 35%, #17497f 70%, #245d9e 100%);
  }
  .cta-line {
    position: absolute;
    left: 32px;
    top: 12px;
    font-family: "Poppins", sans-serif;
    font-weight: 400;
    font-size: 29px;
    color: var(--board-white);
    white-space: nowrap;
  }
  .web-pill {
    position: absolute;
    left: 34px;
    top: 61px;
    width: 461px;
    height: 42px;
    background: var(--board-white);
    border-radius: 2px 24px 24px 2px;
    display: flex;
    align-items: center;
    padding-left: 20px;
    font-family: "Poppins", sans-serif;
    font-size: 29px;
    letter-spacing: 3px;
    color: var(--ink);
  }
  .web-pill .web-domain {
    font-weight: 700;
    color: var(--deep-navy);
  }
</style>
</head>
<body>
  <main class="billboard">
    <div class="brand-name">Brivoqua</div>

    <svg class="headline" viewBox="0 0 610 150" aria-label="Elevate your business with next-gen IT and VOIP services">
      <text class="headline-lead" x="2" y="32" font-size="30" textLength="604" lengthAdjust="spacing">ELEVATE YOUR BUSINESS WITH</text>
      <text class="headline-main" x="0" y="107" font-size="86" textLength="606" lengthAdjust="spacingAndGlyphs">NEXT-GEN</text>
      <text class="headline-sub" x="2" y="145" font-size="38" textLength="604" lengthAdjust="spacingAndGlyphs">IT AND VOIP SERVICES</text>
    </svg>

    <svg class="tagline-band" viewBox="0 0 824 51" aria-hidden="true">
      <polygon points="24,0 800,0 824,51 0,51" fill="var(--sky-blue)"/>
    </svg>
    <p class="tagline-text">Innovative IT and VOIP Solutions Tailored for Your Business Success</p>

    <section class="cta-panel">
      <div class="team-photo" role="img" aria-label="Business team working at computers around a conference table in a blue-lit tech office"></div>
      <p class="cta-line">Transform Your Tech Today at</p>
      <p class="web-pill">www.<span class="web-domain">brivoqua</span>.com</p>
    </section>
  </main>
</body>
</html>
```